Mastering Modern Vineyard Management

size of the ad - 8”x 10.75" plus 0.25" bleed
I would like an ad for a magazine that will stand out and make people want to read the ad.
The ad should not be crowded and people reading the ad will be able to read the text.
I would like it to be a creative and modern-day design.
the list of topics should not be the focus of the ad.
the text is attached.
If you decide to use people in the ad then please no ladies.
please note that leave over 1 inch for the bottom of the footer

```html
<!DOCTYPE html>
<html lang="en">
<head>
<meta charset="UTF-8">
<title>Real Estate Course – Magazine Ad</title>
<link rel="stylesheet" href="https://fonts.googleapis.com/css2?family=Poppins:wght@400;500;600;700;800;900&display=swap">
<style>
  :root {
    --navy: #0b1a33;
    --navy-deep: #081428;
    --blue: #0a8cf5;
    --blue-bright: #1b95ff;
    --white: #ffffff;
    --red: #ee1c25;
    --rule: rgba(255,255,255,0.35);
    --page-bg: #ffffff;
  }
  * { margin: 0; padding: 0; box-sizing: border-box; }
  html, body { width: 800px; height: 1200px; overflow: hidden; background: var(--page-bg); }
  body { font-family: "Poppins", sans-serif; color: var(--white); }

  .ad { position: relative; width: 800px; height: 1200px; background: var(--page-bg); overflow: hidden; }
  .ad-body { position: absolute; left: 0; top: 0; width: 800px; height: 1056px; background: var(--navy); overflow: hidden; }

  .hero-photo {
    position: absolute; left: 300px; top: 0; width: 500px; height: 560px;
    background:
      radial-gradient(circle at 56% 48%, rgba(255,235,210,0.9) 0, rgba(120,190,255,0.55) 7%, rgba(30,90,160,0.35) 22%, transparent 45%),
      radial-gradient(ellipse at 75% 40%, #1d4f86 0, #123764 40%, transparent 75%),
      linear-gradient(90deg, var(--navy) 0%, rgba(11,26,51,0.2) 30%, #163e6e 70%, #0f2d52 100%);
  }
  .hero-fade {
    position: absolute; left: 0; top: 380px; width: 800px; height: 220px;
    background: linear-gradient(180deg, transparent, var(--navy) 85%);
  }
  .hero-left-glow {
    position: absolute; left: 0; top: 0; width: 420px; height: 560px;
    background: radial-gradient(ellipse at 30% 30%, #1a4a7c 0, rgba(16,45,80,0.6) 45%, transparent 80%);
  }

  .title { position: absolute; left: 48px; top: 54px; font-weight: 800; line-height: 1; }
  .title-line { display: block; letter-spacing: -1px; }
  .title-real { font-size: 164px; line-height: 140px; }
  .title-estate { font-size: 112px; line-height: 96px; }
  .title-course { font-size: 108px; line-height: 92px; color: var(--blue); }

  .subtitle { position: absolute; left: 51px; top: 412px; font-weight: 700; font-size: 25px; line-height: 35px; }

  .tagline {
    position: absolute; left: 51px; top: 510px; width: 702px; height: 62px;
    background: var(--blue); border-radius: 10px;
    display: flex; align-items: center; justify-content: center;
    font-weight: 700; font-size: 19px; letter-spacing: 0.1px; white-space: nowrap;
  }

  .details { position: absolute; left: 54px; top: 612px; width: 311px; }
  .location { color: var(--blue); font-weight: 800; font-size: 30px; line-height: 40px; }
  .sessions { font-weight: 600; font-size: 19px; line-height: 26px; margin-top: 4px; }
  .rule { height: 1px; background: var(--rule); }
  .sessions + .rule { margin-top: 12px; }
  .date { display: flex; align-items: center; height: 120px; }
  .date-label { writing-mode: vertical-rl; transform: rotate(180deg); font-size: 13px; letter-spacing: 1px; margin-right: 6px; }
  .date-day { color: var(--blue); font-weight: 800; font-size: 104px; line-height: 1; letter-spacing: -2px; }
  .date-month { margin-left: 14px; font-size: 35px; line-height: 40px; font-weight: 400; }
  .scholarships { font-weight: 700; font-size: 21px; line-height: 54px; }
  .early-bird { color: var(--red); font-weight: 800; font-size: 30px; line-height: 52px; }
  .audience { font-size: 18px; line-height: 25px; margin-top: 14px; }

  .topics { position: absolute; left: 420px; top: 612px; }
  .topics-title { color: var(--blue); font-weight: 800; font-size: 30px; line-height: 40px; margin-bottom: 8px; }
  .topic-list { list-style: none; }
  .topic-list li { display: flex; align-items: center; font-size: 18px; line-height: 32.6px; }
  .topic-list svg { width: 16px; height: 16px; margin-right: 13px; flex: none; }

  .footer-band { position: absolute; left: 0; top: 1010px; width: 800px; height: 46px; }
</style>
</head>
<body>
<div class="ad">
  <section class="ad-body">
    <div class="hero-photo" role="img" aria-label="Businessman in a dark suit holding a glowing line drawing of city skyscrapers in his open hand"></div>
    <div class="hero-left-glow"></div>
    <div class="hero-fade"></div>

    <h1 class="title">
      <span class="title-line title-real">REAL</span>
      <span class="title-line title-estate">ESTATE</span>
      <span class="title-line title-course">COURSE</span>
    </h1>

    <p class="subtitle">MASTERING MODERN<br>VINEYARD MANAGEMENT</p>

    <div class="tagline">INVESTING IN KNOWLEDGE IS INVESTING IN OPPORTUNITIES</div>

    <div class="details">
      <h2 class="location">LARKHAVEN</h2>
      <p class="sessions">10 -Tuesday evenings sessions</p>
      <div class="rule"></div>
      <div class="date">
        <span class="date-label">STARTING</span>
        <span class="date-day">28</span>
        <span class="date-month">FEBRUARY<br>2023</span>
      </div>
      <div class="rule"></div>
      <p class="scholarships">Limited Partial Scholarships</p>
      <div class="rule"></div>
      <p class="early-bird">EARLY BIRD SPECIAL</p>
      <div class="rule"></div>
      <p class="audience">For those that started or would like<br>to go into real estate</p>
    </div>

    <div class="topics">
      <h2 class="topics-title">PARTIAL LISTING</h2>
      <ul class="topic-list">
        <li><svg viewBox="0 0 16 16"><circle cx="8" cy="8" r="8" fill="#0a8cf5"/><path d="M4.5 8.2l2.3 2.2 4.7-4.8" fill="none" stroke="#0b1a33" stroke-width="2"/></svg>Real estate investment strategies</li>
        <li><svg viewBox="0 0 16 16"><circle cx="8" cy="8" r="8" fill="#0a8cf5"/><path d="M4.5 8.2l2.3 2.2 4.7-4.8" fill="none" stroke="#0b1a33" stroke-width="2"/></svg>Due diligence</li>
        <li><svg viewBox="0 0 16 16"><circle cx="8" cy="8" r="8" fill="#0a8cf5"/><path d="M4.5 8.2l2.3 2.2 4.7-4.8" fill="none" stroke="#0b1a33" stroke-width="2"/></svg>Financing</li>
        <li><svg viewBox="0 0 16 16"><circle cx="8" cy="8" r="8" fill="#0a8cf5"/><path d="M4.5 8.2l2.3 2.2 4.7-4.8" fill="none" stroke="#0b1a33" stroke-width="2"/></svg>Underwriting</li>
        <li><svg viewBox="0 0 16 16"><circle cx="8" cy="8" r="8" fill="#0a8cf5"/><path d="M4.5 8.2l2.3 2.2 4.7-4.8" fill="none" stroke="#0b1a33" stroke-width="2"/></svg>Property management</li>
        <li><svg viewBox="0 0 16 16"><circle cx="8" cy="8" r="8" fill="#0a8cf5"/><path d="M4.5 8.2l2.3 2.2 4.7-4.8" fill="none" stroke="#0b1a33" stroke-width="2"/></svg>Real estate Legal basics</li>
        <li><svg viewBox="0 0 16 16"><circle cx="8" cy="8" r="8" fill="#0a8cf5"/><path d="M4.5 8.2l2.3 2.2 4.7-4.8" fill="none" stroke="#0b1a33" stroke-width="2"/></svg>Sourcing deals</li>
        <li><svg viewBox="0 0 16 16"><circle cx="8" cy="8" r="8" fill="#0a8cf5"/><path d="M4.5 8.2l2.3 2.2 4.7-4.8" fill="none" stroke="#0b1a33" stroke-width="2"/></svg>Syndication</li>
        <li><svg viewBox="0 0 16 16"><circle cx="8" cy="8" r="8" fill="#0a8cf5"/><path d="M4.5 8.2l2.3 2.2 4.7-4.8" fill="none" stroke="#0b1a33" stroke-width="2"/></svg>Dealing with brokers</li>
        <li><svg viewBox="0 0 16 16"><circle cx="8" cy="8" r="8" fill="#0a8cf5"/><path d="M4.5 8.2l2.3 2.2 4.7-4.8" fill="none" stroke="#0b1a33" stroke-width="2"/></svg>Tax fundamentals</li>
      </ul>
    </div>

    <svg class="footer-band" viewBox="0 0 800 46" preserveAspectRatio="none" aria-hidden="true">
      <polygon points="425,10 800,10 800,46 390,46" fill="#ffffff"/>
      <polygon points="432,17 800,17 800,46 402,46" fill="#0a8cf5"/>
    </svg>
  </section>
</div>
</body>
</html>
```